Banner to be displayed at local Farmers Market Booth.

Graphic Design Brief: Farmers Market Banner Contest

Project Overview:We are seeking talented graphic designers to create a visually appealing banner for our booth at the local farmers market. Our company specializes in healthy, all-natural dog and cat treats, and we want a banner that captures our brand identity while drawing in pet owners who value quality and nutrition for their furry friends.

Banner Specifications:

Size: 24 inches x 60 inches (Horizontal orientation) 24" High X 60 wide

Theme: Vintage/Retro

Style: Warm, inviting, nostalgic with a touch of rustic charm

Colors: Earthy, muted tones such as warm browns, soft greens, and creamy yellows. Pops of red or blue may be used sparingly for accents. OR Black and White with gray scales. Would like to see both

Typography: Retro-style fonts that are readable and align with the vintage aesthetic.

Key Elements to Include: website (www.moltbyfarms.com)

Company Name: Moltby Farms

Tagline: " Simply Honest Bites "
Imagery: Illustrations or stylized graphics of happy dogs and cats, possibly interacting with treats.

Emphasis on Natural Ingredients: Icons or design elements that subtly suggest freshness and quality (e.g., leaves, wheat, bones, or paw prints).

Farmers Market Appeal: A design that blends well with the artisanal, handmade, and farm-fresh atmosphere of the market.

Design Considerations:

The banner should be easily readable from a distance.

A balanced composition that doesn't feel overcrowded.

Should evoke trust and warmth while maintaining a professional look.

Avoid overly modern or sleek elements that don’t align with the vintage aesthetic.

Submission Requirements:

High-resolution digital file in PDF or AI format.

CMYK color mode for printing purposes.

Must include a mockup or preview of how it would look in a real farmers market setting.

We look forward to seeing your creative interpretations of our brand! If you have any questions, feel free to reach out.

Font styles to use
Other font styles liked:
• See attachement

Requirements
Nice to have
• Retro/Vintage,playful BUT NOT whimsical

```html
<!DOCTYPE html>
<html lang="en">
<head>
<meta charset="utf-8">
<title>Moltby Farms – Market Banner</title>
<link rel="stylesheet" href="https://fonts.googleapis.com/css2?family=Archivo+Black&family=Playfair+Display:wght@700;900&display=swap">
<style>
  :root {
    --page: #ffffff;
    --mint: #5ce1b0;
    --tan: #edbf78;
    --ink: #13231f;
    --paper-edge: #ffffff;
    --art-light: #e9ecea;
    --art-dark: #6f7472;
  }
  html, body {
    margin: 0;
    padding: 0;
    width: 1200px;
    height: 576px;
    overflow: hidden;
    background: var(--page);
  }
  .banner {
    display: block;
    width: 1200px;
    height: 576px;
  }
  .field-mint { fill: var(--mint); }
  .field-tan { fill: var(--tan); stroke: var(--paper-edge); stroke-width: 3; stroke-linejoin: round; }
  .tagline {
    font-family: "Archivo Black", "Arial Black", sans-serif;
    font-size: 64px;
    fill: var(--ink);
  }
  .website {
    font-family: "Playfair Display", Georgia, serif;
    font-weight: 700;
    font-size: 27px;
    letter-spacing: 6px;
    fill: var(--ink);
  }
  .company-name {
    font-family: "Playfair Display", Georgia, serif;
    font-weight: 900;
    font-size: 48px;
    letter-spacing: 4px;
    fill: var(--ink);
  }
  .company-name-shadow { fill: var(--paper-edge); }
  .descriptor {
    font-family: "Playfair Display", Georgia, serif;
    font-weight: 700;
    font-size: 38px;
    fill: var(--ink);
  }
  .brand-mark-name {
    font-family: "Playfair Display", Georgia, serif;
    font-weight: 700;
    font-size: 17px;
    fill: var(--paper-edge);
  }
  .brand-mark-dot { fill: none; stroke: var(--paper-edge); stroke-width: 2; }
  .pet-art { fill: url(#pet-art-tone); stroke: var(--paper-edge); stroke-width: 3; }
</style>
</head>
<body>
<svg class="banner" viewBox="0 0 1200 576" xmlns="http://www.w3.org/2000/svg">
  <defs>
    <linearGradient id="pet-art-tone" x1="0" y1="0" x2="1" y2="1">
      <stop offset="0" stop-color="var(--art-light)"/>
      <stop offset="1" stop-color="var(--art-dark)"/>
    </linearGradient>
  </defs>

  <rect class="field-mint" x="69" y="54" width="1083" height="432"/>

  <path class="field-tan" d="M69 331 L117 324 L155 319 L178 338 L211 328 L253 356 L281 345 L328 366 L361 342 L422 328 L469 342 L516 328 L563 356 L610 342 L657 328 L704 338 L727 347 L1135 356 L1152 352 L1152 486 L69 486 Z"/>

  <text class="tagline" x="705" y="192" text-anchor="end" textLength="600" lengthAdjust="spacingAndGlyphs">SIMPLY HONEST</text>
  <text class="tagline" x="705" y="259" text-anchor="end" textLength="330" lengthAdjust="spacingAndGlyphs">BITES</text>

  <text class="website" x="150" y="307" textLength="525" lengthAdjust="spacingAndGlyphs">WWW.MOLTBYFARMS.COM</text>

  <path class="pet-art" role="img" aria-label="Pencil-style illustration of a long-haired dog lying beside a tabby cat"
        d="M735 140 L830 100 L905 112 L960 150 L1015 165 L1060 250 L1120 300 L1135 345 L1130 372 L740 380 L730 300 Z"/>

  <g class="brand-mark">
    <circle class="brand-mark-dot" cx="1024" cy="135" r="9"/>
    <text class="brand-mark-name" x="1040" y="141">Moltby Farms</text>
  </g>

  <text class="company-name company-name-shadow" x="102" y="418" textLength="580" lengthAdjust="spacingAndGlyphs">MOLTBY FARMS</text>
  <text class="company-name" x="105" y="415" textLength="580" lengthAdjust="spacingAndGlyphs">MOLTBY FARMS</text>

  <text class="descriptor" x="102" y="464" textLength="986" lengthAdjust="spacingAndGlyphs">PURVEYORS OF PREMIUM PET FOOD &amp; TREATS</text>
</svg>
</body>
</html>
```